Business Card Design needed for start up company Halvora

In need of a new business card designed for a start up company based in Sydney, Halvora is a new start up innovative Company, our mission it to make property accessible for everyday Australian and to become the leading Real Estate platform in Australia. We want it to be fresh and clean.

Industry/Entity Type

Financial

Contact Information for Business Card

Section for Name
Section for Title

HALVORA - The Strength of Pooling
Mobile:
Direct:

Font styles to use
Sans Serif

Colors
33a6d7
0692cd
0255a3
ffffff

Requirements
Must have
• Logo, all business card details

```html
<!DOCTYPE html>
<html lang="en">
<head>
<meta charset="utf-8">
<title>Halvora Business Card</title>
<link rel="stylesheet" href="https://fonts.googleapis.com/css2?family=Jost:ital,wght@0,400;0,500;0,700;0,800;1,400&display=swap">
<style>
  :root {
    --sky: #33a6d7;
    --azure: #0692cd;
    --navy: #0255a3;
    --deep: #21447f;
    --white: #ffffff;
    --ink: #4a4f57;
    --ground: #e9ebee;
  }
  * { margin: 0; padding: 0; box-sizing: border-box; }
  html, body { width: 1200px; height: 911px; overflow: hidden; }
  body {
    background: var(--ground);
    font-family: "Jost", sans-serif;
    position: relative;
  }
  .card {
    position: absolute;
    top: 295px;
    width: 560px;
    height: 320px;
    border-radius: 20px;
    overflow: hidden;
    box-shadow: 0 6px 18px rgba(0,0,0,0.18);
  }
  .card-front { left: 25px; background: var(--white); }
  .card-back { left: 615px; background: var(--deep); }

  .side-strip { position: absolute; left: 0; width: 58px; }
  .strip-light { top: 62px; height: 48px; background: var(--azure); }
  .strip-dark { top: 110px; height: 210px; background: var(--deep); }

  .brand {
    position: absolute;
    display: flex;
    align-items: center;
  }
  .brand-dot { border-radius: 50%; flex: none; }
  .brand-name { font-weight: 800; letter-spacing: 0.5px; line-height: 1; }

  .front-brand { left: 26px; top: 78px; }
  .front-brand .brand-dot {
    width: 64px; height: 64px;
    background: var(--sky);
    border: 6px solid var(--white);
    box-sizing: border-box;
  }
  .front-brand .brand-name { font-size: 50px; color: var(--deep); margin-left: 10px; }

  .icon-column {
    position: absolute;
    left: 18px;
    top: 0;
    width: 22px;
    height: 320px;
  }
  .icon-column svg { position: absolute; left: 0; width: 22px; height: 16px; }

  .details { position: absolute; left: 100px; top: 0; color: var(--ink); }
  .details p { position: absolute; left: 0; white-space: nowrap; line-height: 1; }
  .person-name { font-size: 21px; font-weight: 700; color: var(--deep); letter-spacing: 0.4px; }
  .person-title { font-size: 16px; color: var(--azure); }
  .detail-line { font-size: 15px; }

  .back-brand { left: 50%; top: 112px; transform: translateX(-50%); }
  .back-brand .brand-dot { width: 72px; height: 72px; background: var(--white); }
  .back-brand .brand-name { font-size: 62px; color: var(--white); margin-left: 14px; }
  .tagline {
    position: absolute;
    left: 0; right: 0; top: 218px;
    text-align: center;
    color: var(--white);
    font-style: italic;
    font-size: 17px;
    letter-spacing: 0.3px;
  }
</style>
</head>
<body>
  <section class="card card-front">
    <div class="side-strip strip-light"></div>
    <div class="side-strip strip-dark"></div>

    <div class="brand front-brand">
      <span class="brand-dot"></span>
      <span class="brand-name">HALVORA</span>
    </div>

    <div class="icon-column" aria-hidden="true">
      <svg style="top:152px" viewBox="0 0 22 16"><circle cx="11" cy="4.5" r="3.5" fill="#fff"/><path d="M4 16c0-4 3-6.5 7-6.5s7 2.5 7 6.5z" fill="#fff"/></svg>
      <svg style="top:186px" viewBox="0 0 22 16"><path d="M11 0a5.5 5.5 0 0 0-5.5 5.5C5.5 10 11 16 11 16s5.5-6 5.5-10.5A5.5 5.5 0 0 0 11 0z" fill="#fff"/><circle cx="11" cy="5.5" r="2" fill="#21447f"/></svg>
      <svg style="top:226px" viewBox="0 0 22 16"><path d="M6 1l3 3-1.6 2a9 9 0 0 0 4.6 4.6L14 9l3 3-2 3C9 15 4 10 4 3z" fill="#fff"/></svg>
      <svg style="top:245px" viewBox="0 0 22 16"><rect x="7" y="0" width="8" height="16" rx="1.5" fill="#fff"/><rect x="8.5" y="2" width="5" height="10" fill="#21447f"/></svg>
      <svg style="top:266px" viewBox="0 0 22 16"><rect x="3" y="2" width="16" height="12" rx="1" fill="#fff"/><path d="M3.5 3l7.5 6 7.5-6" stroke="#21447f" stroke-width="1.4" fill="none"/></svg>
      <svg style="top:286px" viewBox="0 0 22 16"><circle cx="11" cy="8" r="7" fill="#fff"/><path d="M4 8h14M11 1c-3 4-3 10 0 14M11 1c3 4 3 10 0 14" stroke="#21447f" stroke-width="1.2" fill="none"/></svg>
    </div>

    <div class="details">
      <p class="person-name" style="top:150px">MARA ELLISON</p>
      <p class="person-title" style="top:172px">CEO/FOUNDER</p>
      <p class="detail-line" style="top:188px">41 Harbourline Street</p>
      <p class="detail-line" style="top:206px">Sydney, NSW 2000</p>
      <p class="detail-line" style="top:227px">0412 555 018</p>
      <p class="detail-line" style="top:246px">02 5550 1734</p>
      <p class="detail-line" style="top:267px">mara@halvora.com</p>
      <p class="detail-line" style="top:287px">www.halvora.com</p>
    </div>
  </section>

  <section class="card card-back">
    <div class="brand back-brand">
      <span class="brand-dot"></span>
      <span class="brand-name">HALVORA</span>
    </div>
    <p class="tagline">The Strength of Pooling</p>
  </section>
</body>
</html>
```